Vantro cards

I am in the auto motive, transportation business I would like a business card that is Something cool, modern edgy, having to do with car culture. I offer towing service for high and exotic cars. I also provide towing for collisions and car accidents. I offer open and enclosed transport nationwide.

Target Market(s)

Car culture people high end auto collectors

Industry/Entity Type

Towing car carrier

Contact Information for Business Card

My company colors black yellow and silver

Font styles to use
Serif

```html
<!DOCTYPE html>
<html lang="en">
<head>
<meta charset="utf-8">
<title>Vantro Cards</title>
<link rel="stylesheet" href="https://fonts.googleapis.com/css2?family=Montserrat:wght@600;800&family=Arimo:wght@400&display=swap">
<style>
  :root{
    --bg:#1c1c1c;
    --yellow:#fadf5f;
    --black:#000000;
    --white:#ffffff;
    --ink:#111111;
    --rule:#b5b5b5;
  }
  *{margin:0;padding:0;box-sizing:border-box}
  html,body{width:1200px;height:1015px;overflow:hidden;background:var(--bg)}
  .sheet{width:1200px;height:1015px;display:flex;flex-direction:column;align-items:center;justify-content:center;gap:34px}
  .card{position:relative;width:820px;height:468px;overflow:hidden}

  /* front */
  .card--front{background:var(--yellow)}
  .front-brand{position:absolute;left:0;right:0;top:120px;display:flex;align-items:center;justify-content:center;gap:18px}
  .brand-mark{width:34px;height:34px;background:var(--black)}
  .brand-name{font-family:"Montserrat",sans-serif;font-weight:800;font-size:78px;letter-spacing:4px;color:var(--black);text-transform:uppercase;line-height:1}
  .front-band{position:absolute;left:0;right:0;top:340px;height:64px;background:var(--black);display:flex;align-items:center;justify-content:center}
  .front-url{font-family:"Arimo",sans-serif;font-size:22px;letter-spacing:1px;color:var(--white)}

  /* back */
  .card--back{background:var(--white)}
  .back-brand{position:absolute;left:56px;top:188px;display:flex;align-items:center;gap:12px}
  .back-brand .brand-mark{width:24px;height:24px;background:var(--yellow)}
  .back-brand .brand-name{font-size:52px;letter-spacing:3px}
  .divider{position:absolute;left:400px;top:80px;width:1px;height:250px;background:var(--rule)}
  .contact{position:absolute;left:440px;top:92px;font-family:"Arimo",sans-serif;color:var(--ink)}
  .person-name{font-family:"Montserrat",sans-serif;font-weight:800;font-size:27px;letter-spacing:.5px;line-height:1}
  .person-role{font-family:"Montserrat",sans-serif;font-weight:600;font-size:17px;color:var(--yellow);letter-spacing:.5px;margin-top:4px}
  .contact-list{list-style:none;margin-top:24px}
  .contact-list li{display:flex;align-items:center;gap:12px;font-size:19px;line-height:1.45}
  .contact-list svg{width:18px;height:18px;flex:none}
  .address{margin-top:16px;margin-left:30px;font-size:19px;line-height:1.35}
  .back-strip-black{position:absolute;left:0;bottom:0;width:540px;height:40px;background:var(--black)}
  .back-strip-yellow{position:absolute;right:0;bottom:0;width:282px;height:64px;background:var(--yellow)}
</style>
</head>
<body>
<main class="sheet">
  <section class="card card--front" aria-label="Business card front">
    <div class="front-brand">
      <span class="brand-mark"></span>
      <span class="brand-name">Vantro</span>
    </div>
    <div class="front-band">
      <span class="front-url">www.vantrotransport.com</span>
    </div>
  </section>

  <section class="card card--back" aria-label="Business card back">
    <div class="back-brand">
      <span class="brand-mark"></span>
      <span class="brand-name">Vantro</span>
    </div>
    <div class="divider"></div>
    <div class="contact">
      <p class="person-name">MARCUS HALE</p>
      <p class="person-role">MANAGING DIRECTOR</p>
      <ul class="contact-list">
        <li>
          <svg viewBox="0 0 24 24" aria-hidden="true"><path fill="#fadf5f" d="M6.6 10.8a15.1 15.1 0 0 0 6.6 6.6l2.2-2.2c.3-.3.7-.4 1-.2 1.1.4 2.3.6 3.6.6.6 0 1 .4 1 1V20c0 .6-.4 1-1 1A17 17 0 0 1 3 4c0-.6.4-1 1-1h3.5c.6 0 1 .4 1 1 0 1.3.2 2.5.6 3.6.1.3 0 .7-.2 1z"/></svg>
          044-555 018 240
        </li>
        <li>
          <svg viewBox="0 0 24 24" aria-hidden="true"><path fill="#fadf5f" d="M2 5h20v14H2z"/><path fill="none" stroke="#fff" stroke-width="1.6" d="M2 5l10 8 10-8"/></svg>
          info@vantrotransport.com
        </li>
        <li>
          <svg viewBox="0 0 24 24" aria-hidden="true"><g fill="none" stroke="#fadf5f" stroke-width="2"><circle cx="12" cy="12" r="9"/><path d="M3 12h18M12 3c3 3 3 15 0 18M12 3c-3 3-3 15 0 18"/></g></svg>
          www.vantrotransport.com
        </li>
      </ul>
      <p class="address">218 Carrier Lane, Suite 4<br>Dayton, OH 45120</p>
    </div>
    <div class="back-strip-black"></div>
    <div class="back-strip-yellow"></div>
  </section>
</main>
</body>
</html>
```